Harborline Auto LLC

Car Dealer Customer Service
Address: 2874 Cresthaven Road, Shelbyville, TN 37162
web: www.harborlineautoxq.net
email: harborlineautoxq@mailnest.example
Phone: (931) 555-0148
Phone: (629) 555-0173

```html
<!DOCTYPE html>
<html lang="en">
<head>
<meta charset="utf-8">
<title>Harborline Auto – Business Card</title>
<link href="https://fonts.googleapis.com/css2?family=Lexend:wght@600&family=Poppins:wght@300;400;600&display=swap" rel="stylesheet">
<style>
  :root{
    --backdrop:#2b2b2d;
    --card:#222326;
    --card-edge:#2a2b2f;
    --blue:#2a8fcf;
    --blue-deep:#1f6fa6;
    --gold:#d9a53a;
    --text:#e6e6e6;
    --emboss:#141416;
  }
  *{margin:0;padding:0;box-sizing:border-box}
  html,body{width:1200px;height:1138px;overflow:hidden;background:var(--backdrop)}
  body{position:relative;font-family:"Poppins",sans-serif;color:var(--text)}
  .card{position:absolute;width:620px;height:376px;border-radius:16px;overflow:hidden;
    background:linear-gradient(160deg,var(--card-edge),var(--card) 60%)}
  .card--back{left:290px;top:186px}
  .card--front{left:290px;top:606px}

  /* back */
  .back-mark{position:absolute;left:0;right:0;top:150px;text-align:center;
    font-family:"Lexend",sans-serif;font-weight:600;font-size:44px;letter-spacing:1px;color:var(--emboss)}
  .back-web{position:absolute;left:0;right:0;top:333px;display:flex;justify-content:center;align-items:center;gap:26px;
    font-size:15px;font-weight:400}
  .back-web .rule{width:54px;height:2px;background:var(--gold)}

  /* front */
  .brand{position:absolute;left:34px;top:68px;display:flex;align-items:center;gap:16px}
  .brand-dot{width:28px;height:28px;border-radius:50%;background:var(--gold)}
  .brand-name{font-family:"Lexend",sans-serif;font-weight:600;font-size:40px;color:var(--blue);letter-spacing:.5px}
  .person{position:absolute;left:36px;top:212px}
  .person-name{font-family:"Lexend",sans-serif;font-weight:600;font-size:24px;color:var(--blue)}
  .person-role{font-size:16px;font-weight:300;margin-top:2px}
  .address{position:absolute;left:36px;top:286px;font-size:16px;font-weight:300;line-height:22px}
  .contacts{position:absolute;left:300px;right:16px;top:210px;list-style:none;font-size:15px;font-weight:300;line-height:22px}
  .contacts li{display:flex;align-items:center;gap:8px;white-space:nowrap}
  .contacts svg{width:13px;height:13px;flex:none}
  .contacts .phone{font-weight:600;color:var(--blue);font-size:17px}
  .bands{position:absolute;left:0;bottom:0;width:620px;height:46px}
  .legal{position:absolute;left:304px;top:339px;font-size:16px;font-weight:600;color:#fff}
</style>
</head>
<body>

<section class="card card--back" aria-label="Card back">
  <div class="back-mark">HARBORLINE AUTO</div>
  <div class="back-web"><span class="rule"></span>www.harborlineautoxq.net<span class="rule"></span></div>
</section>

<section class="card card--front" aria-label="Card front">
  <div class="brand">
    <span class="brand-dot"></span>
    <span class="brand-name">HARBORLINE AUTO</span>
  </div>

  <div class="person">
    <div class="person-name">Marek Jolley</div>
    <div class="person-role">Managing Director</div>
  </div>
  <div class="address">2874 Cresthaven Road,<br>Shelbyville, TN 37162</div>

  <ul class="contacts">
    <li><svg viewBox="0 0 16 16"><path fill="#d9a53a" d="M2 5c0-2 2-3 6-3s6 1 6 3v1h-3V5H5v1H2zM4 7h8l2 6H2z"/></svg><span class="phone">931-555-0148</span></li>
    <li><svg viewBox="0 0 16 16"><path fill="#d9a53a" d="M2 5c0-2 2-3 6-3s6 1 6 3v1h-3V5H5v1H2zM4 7h8l2 6H2z"/></svg><span class="phone">629-555-0173</span></li>
    <li><svg viewBox="0 0 16 16"><rect x="1" y="3" width="14" height="10" fill="#d9a53a"/><path d="M1 3l7 6 7-6" fill="none" stroke="#222326" stroke-width="1.4"/></svg>www.harborlineautoxq.net</li>
    <li><svg viewBox="0 0 16 16"><circle cx="8" cy="8" r="6.5" fill="none" stroke="#d9a53a" stroke-width="1.5"/><path d="M1.5 8h13M8 1.5c-3 3.5-3 9.5 0 13M8 1.5c3 3.5 3 9.5 0 13" fill="none" stroke="#d9a53a" stroke-width="1.2"/></svg>harborlineautoxq@mailnest.example</li>
  </ul>

  <svg class="bands" viewBox="0 0 620 46" preserveAspectRatio="none" aria-hidden="true">
    <rect x="0" y="32" width="246" height="14" fill="var(--gold)"/>
    <path d="M252 0H620V46H236Z" fill="var(--blue-deep)"/>
  </svg>
  <div class="legal">HARBORLINE AUTO LLC</div>
</section>

</body>
</html>
```